i would like a business card to leave with customers and potential customers for electrical work and for the supply and install of reverse cycle airconditioning in the domestic and commercial market.
I own my own business and im a sole trader. I have an a'class electrical lisence and also a refrigeration lisence so i am
able to offer complete installations in airconditioning by a fully qualified and lisenced tradesman.
im looking for something that comes across as unique and professional.
i had the coluor black and some gold in mind but open to any coluors.
something like Lanterra Electrical & Refrigeration
or Lanterra Air.
i will use this design on a business card to advertise through summer to help generate installs through the busy season.

Target Market(s)

Mainly domestic house holds through summer who are in need of airconditioning and reliable information to acomadate thier cooling and heating requirements

Industry/Entity Type

Electrical

Requirements
Must have
• Business name- Lanterra
My name- Mark Delford
My mobile no- 0438 517 290
My email- mrdelford@qelvo.com.au
Installation & Decomissioning of aiconditioning split systems
LIC NO: TRK 540316
Nice to have
• Lanterra Electrical & Refrigeration

```html
<!DOCTYPE html>
<html lang="en">
<head>
<meta charset="utf-8">
<title>Lanterra Electrical &amp; Refrigeration – Business Card</title>
<link rel="stylesheet" href="https://fonts.googleapis.com/css2?family=Montserrat:wght@500;600;700;800&display=swap">
<style>
  :root {
    --backdrop: #3a3a3a;
    --card-light: #fbfbfb;
    --card-shade: #e4e4e4;
    --card-base: #0d0d0d;
    --brand-red: #e41e26;
    --ink: #1a1a1a;
    --badge-fill: #b9c3c8;
  }
  * { margin: 0; padding: 0; box-sizing: border-box; }
  html, body {
    width: 1200px; height: 585px; overflow: hidden;
    background: var(--backdrop);
    font-family: "Montserrat", Arial, sans-serif;
    color: var(--ink);
  }
  .canvas { position: relative; width: 1200px; height: 585px; }
  .card {
    position: absolute; top: 228px;
    width: 586px; height: 334px;
    border-radius: 14px; overflow: hidden;
    background: var(--card-base);
    box-shadow: 0 6px 16px rgba(0,0,0,.45);
  }
  .card--front { left: 9px; }
  .card--back { left: 604px; }
  .card__texture {
    position: absolute; left: 0; right: 0; top: 0; bottom: 18px;
    border-radius: 14px 14px 12px 12px;
    background:
      radial-gradient(ellipse at 35% 40%, var(--card-light) 0%, #f1f1f1 45%, var(--card-shade) 100%);
  }
  .wordmark {
    position: absolute; left: 0; right: 0; text-align: center;
    font-weight: 800; color: var(--brand-red);
    letter-spacing: 1px; line-height: 1;
  }
  .tagline {
    position: absolute; left: 0; right: 0; text-align: center;
    font-weight: 600; font-variant: small-caps; letter-spacing: 1.2px;
    color: var(--ink); line-height: 1;
  }
  .card--front .wordmark { top: 110px; font-size: 70px; }
  .card--front .tagline { top: 200px; font-size: 19px; }
  .card--back .wordmark { top: 53px; font-size: 48px; }
  .card--back .tagline { top: 107px; font-size: 14px; }
  .contact-name {
    position: absolute; top: 168px; left: 0; right: 0; text-align: center;
    font-size: 19px; font-weight: 700; color: var(--brand-red); letter-spacing: .3px;
  }
  .contact-row {
    position: absolute; top: 197px; font-size: 15px; font-weight: 500;
    display: flex; align-items: center; gap: 8px;
  }
  .contact-row--phone { left: 84px; }
  .contact-row--email { left: 240px; }
  .credential-badge {
    position: absolute; left: 64px; top: 235px; width: 30px; height: 30px;
    background: var(--badge-fill);
  }
  .credential-text {
    position: absolute; left: 102px; top: 231px;
    font-size: 14.5px; font-weight: 500; line-height: 22px;
  }
</style>
</head>
<body>
<main class="canvas">
  <section class="card card--front">
    <div class="card__texture" role="img" aria-label="Soft light grey background of layered translucent squares"></div>
    <p class="wordmark">Lanterra</p>
    <p class="tagline">Lanterra Electrical &amp; Refrigeration</p>
  </section>

  <section class="card card--back">
    <div class="card__texture" role="img" aria-label="Soft light grey background of layered translucent squares"></div>
    <p class="wordmark">Lanterra</p>
    <p class="tagline">Lanterra Electrical &amp; Refrigeration</p>
    <p class="contact-name">MARK DELFORD</p>
    <p class="contact-row contact-row--phone">
      <svg width="12" height="20" viewBox="0 0 12 20" aria-hidden="true">
        <rect x="1" y="1" width="10" height="18" rx="2" fill="none" stroke="#1a1a1a" stroke-width="1.6"/>
        <line x1="4.5" y1="16" x2="7.5" y2="16" stroke="#1a1a1a" stroke-width="1.4"/>
      </svg>
      0438 517 290
    </p>
    <p class="contact-row contact-row--email">
      <svg width="18" height="13" viewBox="0 0 18 13" aria-hidden="true">
        <rect x="1" y="1" width="16" height="11" fill="none" stroke="#1a1a1a" stroke-width="1.4"/>
        <polyline points="1,1 9,7.5 17,1" fill="none" stroke="#1a1a1a" stroke-width="1.4"/>
      </svg>
      MRDELFORD@QELVO.COM.AU
    </p>
    <div class="credential-badge" role="img" aria-label="Licence authorisation badge"></div>
    <p class="credential-text">Installation &amp; Decomissioning of airconditioning split systems<br>LIC NO: TRK 540316</p>
  </section>
</main>
</body>
</html>
```